Stationery Design Project

Our company is "Meridian Systems" and we have a product called "lunogrid.com". The product is an online accounting software for businesses. We want to communicate that our software will help business owners to be more efficient and help them track their finances better. Lunogrid.com is basically a simple version of ledgerpal.

"We want a unique and creative design which will surprise our customer."

NAME CARD = LUNOGRID
We want a lunogrid name card NOT MERIDIAN SYSTEMS.

For the content of the name card, please make sure it fit with a long name like the following:

Rudi Wahyo Alias Rudi
Developer Specialist
T: (021) 4827 1036
F: (021) 4827 1037
E: customer.service@mrdn-sys.example

I need you to put it the following information to the name card

"lunogrid"
- moto is "automate your businesses"
- website "www.lunogrid.com"
- lunogrid is a "Web Accounting Software"
- product of "Meridian Systems"

LETTERHEAD, ENVELOPE, FOLDER = MERIDIAN SYSTEMS
Other than name card we wanted you to design for us; letterhead, envelope and folder. In letterhead, envelope and folder it should ONLY contain the following information ("Meridian Systems").
PLEASE BE SURE YOU ARE NOT PUTTING "LUNOGRID LOGO" IN LETTERHEAD, ENVELOPE AND FOLDER.

"Meridian Systems"
Address:
Ruko Graha Pelangi Blok. D No. 18
Jl. Kenanga Raya No. 71
Jakarta
Cempaka, 11470
Indonesia

Web Address: mrdn-sys.example

T: (021) 4827 1036
F: (021) 4827 1037

Target Market(s)

Business Owners, Accountant, Auditor, Tax Consultant

Industry/Entity Type

Accounting

Requirements

```html
<!DOCTYPE html>
<html lang="en">
<head>
<meta charset="utf-8">
<title>Lunogrid Name Card</title>
<link rel="stylesheet" href="https://fonts.googleapis.com/css2?family=PT+Sans:wght@400;700&family=Share+Tech+Mono&display=swap">
<style>
  :root {
    --stage: #b9b9b9;
    --card-edge: #1657a3;
    --card-mid: #1f86c9;
    --card-glow: #2bbbe6;
    --ink-white: #ffffff;
    --ink-soft: #c9e3f3;
    --ink-muted: #9cc3dc;
    --ink-brand: #56626d;
    --mark-fill: #7d8a94;
    --rule: rgba(200, 225, 240, 0.55);
  }
  * { margin: 0; padding: 0; box-sizing: border-box; }
  html, body {
    width: 1200px; height: 960px; overflow: hidden;
    background: var(--stage);
  }
  .stage { position: relative; width: 1200px; height: 960px; }
  .card {
    position: absolute; overflow: hidden;
    background: radial-gradient(ellipse 70% 75% at 45% 45%, var(--card-glow) 0%, var(--card-mid) 45%, var(--card-edge) 100%);
    font-family: "PT Sans", sans-serif;
  }
  .card--front { left: 265px; top: 60px; width: 701px; height: 414px; }
  .card--back  { left: 269px; top: 510px; width: 693px; height: 410px; }
  .ring-decor {
    position: absolute; border-radius: 50%;
    background: radial-gradient(circle, rgba(40,110,190,0.35) 0%, rgba(60,170,225,0.25) 45%, rgba(90,200,240,0.12) 62%, rgba(255,255,255,0) 72%);
  }
  .card--front .ring-decor { left: 390px; top: -30px; width: 420px; height: 420px; }
  .card--back .ring-decor { left: 330px; top: -20px; width: 440px; height: 440px; }
  .abs { position: absolute; white-space: nowrap; }
  .brand-dot { position: absolute; border-radius: 50%; background: var(--mark-fill); }
  .brand-name { color: var(--ink-brand); font-weight: 400; letter-spacing: 0.06em; text-transform: uppercase; line-height: 1; }
  .brand-kind, .brand-web { color: var(--ink-white); font-size: 17px; line-height: 1; }
  .maker-name { color: var(--ink-white); font-size: 29px; font-weight: 400; line-height: 1; }
  .maker-label { font-family: "Share Tech Mono", monospace; color: var(--ink-soft); font-size: 11px; letter-spacing: 0.14em; line-height: 1; }
  .motto, .maker-web { color: var(--ink-white); font-size: 18px; line-height: 1; }
  .divider { position: absolute; left: 41px; top: 250px; width: 618px; height: 1px; background: var(--rule); }
  .person-name { color: var(--ink-white); font-size: 25px; font-weight: 700; line-height: 1; }
  .person-role { font-family: "Share Tech Mono", monospace; color: var(--ink-muted); font-size: 15px; letter-spacing: 0.14em; line-height: 1; }
  .contact { color: var(--ink-soft); font-size: 18px; line-height: 1; }
</style>
</head>
<body>
<main class="stage">
  <section class="card card--front">
    <div class="ring-decor" role="img" aria-label="Soft concentric ring decoration"></div>

    <div class="brand-dot" style="left:47px;top:34px;width:66px;height:66px;"></div>
    <div class="abs brand-name" style="left:121px;top:52px;font-size:26px;">lunogrid</div>
    <div class="abs brand-kind" style="left:121px;top:93px;">Web Accounting Software</div>
    <div class="abs brand-web" style="left:121px;top:114px;">www.lunogrid.com</div>

    <div class="abs maker-name" style="left:47px;top:146px;">Meridian Systems</div>
    <div class="abs maker-label" style="left:47px;top:179px;">A PRODUCT FOR LUNOGRID USERS</div>
    <div class="abs motto" style="left:47px;top:194px;">automate your businesses</div>
    <div class="abs maker-web" style="left:47px;top:216px;">www.mrdn-sys.example</div>

    <div class="abs person-name" style="left:368px;top:220px;">Rudi Wahyo Alias Rudi</div>
    <div class="divider"></div>
    <div class="abs person-role" style="left:368px;top:258px;">DEVELOPER SPECIALIST</div>
    <div class="abs contact" style="left:368px;top:299px;">T: (021) 4827 1036</div>
    <div class="abs contact" style="left:368px;top:326px;">F: (021) 4827 1037</div>
    <div class="abs contact" style="left:368px;top:353px;">E: customer.service@mrdn-sys.example</div>
  </section>

  <section class="card card--back">
    <div class="ring-decor" role="img" aria-label="Soft concentric ring decoration"></div>
    <div class="brand-dot" style="left:83px;top:148px;width:108px;height:108px;"></div>
    <div class="abs brand-name" style="left:207px;top:178px;font-size:46px;">lunogrid</div>
  </section>
</main>
</body>
</html>
```